UI/ UX Design for ERP Software

We need a new UX/UI interface for a ERP software for property managers. Our CMMS / ERP solution is made based on responsive design technologies and is coded in PHP.
The overall UX to be similar to Tev Ulna - easy navigation, intuitive menus.

Industry/Entity Type

Property Management

Number of Pages Required

5+ page

Requirements
Must have
• Round dock buttons
Consistent icons across the application
Enough Spacing between buttons/icons/ menu
Consistent Font
Nice to have
• We would like the UX to allow the users to use the application without /minimum training.
Should not have
• we don't want anything that is classic with respect to UX

```html
<!DOCTYPE html>
<html lang="en">
<head>
<meta charset="utf-8">
<title>Keyvane – Active dashboard</title>
<link href="https://fonts.googleapis.com/css2?family=Roboto:wght@300;400;500;700&family=IBM+Plex+Sans:wght@400;500&display=swap" rel="stylesheet">
<style>
  :root{
    --page-bg:#e6f3f9;
    --surface:#ffffff;
    --primary:#0a7cf5;
    --accent:#0aa7f0;
    --title:#12a9ef;
    --ink:#111418;
    --muted:#3a3f45;
    --grid:#b9bcbf;
    --bar:#82b4e9;
    --c-sched:#82b4e9;
    --c-done:#93e884;
    --c-future:#f5a45d;
    --c-orders:#43434a;
    --c-orders-done:#8686e8;
    --c-insp:#f25c84;
    --c-insp-done:#e5d456;
  }
  *{box-sizing:border-box;margin:0;padding:0}
  html,body{width:1092px;height:1200px;overflow:hidden}
  body{background:var(--page-bg);font-family:"Roboto",sans-serif;color:var(--ink);position:relative}
  .topbar{position:absolute;left:0;top:0;width:1092px;height:72px;background:var(--surface)}
  .brand{position:absolute;left:32px;top:20px;display:flex;align-items:center;gap:8px;font:700 26px "Roboto",sans-serif;color:var(--primary)}
  .brand-mark{width:20px;height:20px;border-radius:50%;background:var(--primary)}
  .menu-toggle{position:absolute;left:232px;top:27px}
  .search{position:absolute;left:363px;top:18px;width:307px;height:35px;display:flex;border:1px solid #8aa0b4;border-radius:2px;overflow:hidden}
  .search span{flex:1;padding:0 16px;line-height:33px;font-size:15px;color:#666;font-family:"IBM Plex Sans",sans-serif}
  .search button{width:48px;border:0;background:var(--accent);display:flex;align-items:center;justify-content:center}
  .icon-btn{position:absolute;top:20px}
  .badge{position:absolute;top:-3px;right:-6px;width:14px;height:14px;border-radius:50%;background:var(--accent);color:#fff;font-size:10px;line-height:14px;text-align:center}
  .avatar{position:absolute;left:953px;top:11px;width:50px;height:50px;border-radius:50%;background:radial-gradient(circle at 50% 40%,#c9a27f,#7a6a5a)}
  .page-title{position:absolute;left:118px;top:104px;font:300 32px "Roboto",sans-serif;color:var(--title)}
  .stat{position:absolute;top:193px;height:189px;background:var(--surface);text-align:center}
  .stat h3{font:500 11.5px "Roboto",sans-serif;letter-spacing:.3px;margin-top:31px}
  .stat .value{font:500 15.5px "Roboto",sans-serif;margin-top:15px}
  .stat svg{position:absolute;left:50%;transform:translateX(-50%);bottom:30px}
  .stat.plain h3{margin-top:50px}
  .range{position:absolute;top:418px;height:54px;background:var(--surface);display:flex;align-items:center;justify-content:center;gap:5px;font:400 14px "Roboto",sans-serif;color:#222}
  .chart-panel{position:absolute;left:121px;top:519px;width:852px;height:390px;background:var(--surface);box-shadow:0 1px 3px rgba(0,0,0,.12)}
  .chart-panel text{font-family:"IBM Plex Sans",sans-serif;fill:#111}
  .legend-item{position:absolute;width:196px;height:71px;background:var(--surface);box-shadow:0 1px 3px rgba(0,0,0,.12);display:flex;align-items:center;padding-left:14px;gap:14px;font:500 14.5px/22px "IBM Plex Sans",sans-serif}
  .swatch{width:26px;height:29px;flex:none}
  .footer{position:absolute;left:0;width:1092px;top:1153px;text-align:center;font:400 14px "Roboto",sans-serif;color:#333}
</style>
</head>
<body>
<header class="topbar">
  <div class="brand"><span class="brand-mark"></span>Keyvane</div>
  <svg class="menu-toggle" width="25" height="18" viewBox="0 0 25 18"><rect y="0" width="25" height="2.4" fill="#111"/><rect y="7.8" width="25" height="2.4" fill="#111"/><rect y="15.6" width="25" height="2.4" fill="#111"/></svg>
  <div class="search"><span>Search</span><button aria-label="Search"><svg width="15" height="15" viewBox="0 0 15 15"><circle cx="6" cy="6" r="4.3" fill="none" stroke="#fff" stroke-width="2"/><line x1="9.2" y1="9.2" x2="13" y2="13" stroke="#fff" stroke-width="2.4" stroke-linecap="round"/></svg></button></div>
  <div class="icon-btn" style="left:842px"><svg width="24" height="28" viewBox="0 0 24 28"><path d="M12 3c-5 0-7 4-7 8v6l-3 4h20l-3-4v-6c0-4-2-8-7-8z" fill="none" stroke="#111" stroke-width="1.8"/><path d="M9 23a3 3 0 0 0 6 0" fill="none" stroke="#111" stroke-width="1.8"/></svg><span class="badge">6</span></div>
  <div class="icon-btn" style="left:893px"><svg width="28" height="28" viewBox="0 0 28 28"><path d="M3 5h22v14H11l-6 5v-5H3z" fill="none" stroke="#111" stroke-width="1.8" stroke-linejoin="round"/><line x1="8" y1="10" x2="20" y2="10" stroke="#111" stroke-width="1.6"/><line x1="8" y1="14" x2="20" y2="14" stroke="#111" stroke-width="1.6"/></svg><span class="badge">6</span></div>
  <div class="avatar" role="img" aria-label="User profile photo"></div>
</header>

<h1 class="page-title">Active dashboard</h1>

<section class="stat plain" style="left:117px;width:135px">
  <h3>PROPERTIES</h3>
  <svg width="66" height="54" viewBox="0 0 66 54"><path d="M33 3 L3 27 l5 5 L33 12 l25 20 l5-5 L50 17 V5 h-8 v6z" fill="var(--primary)"/><path d="M11 30 L33 13 L55 30 V52 H40 V36 H26 V52 H11z" fill="var(--primary)"/></svg>
</section>
<section class="stat plain" style="left:271px;top:194px;height:186px;width:139px">
  <h3>TENANTS</h3>
  <svg width="60" height="52" viewBox="0 0 60 52"><circle cx="30" cy="11" r="10" fill="var(--primary)"/><circle cx="10" cy="19" r="7" fill="var(--primary)"/><circle cx="50" cy="19" r="7" fill="var(--primary)"/><path d="M16 52 V35 a8 8 0 0 1 8-8 h12 a8 8 0 0 1 8 8 V52z" fill="var(--primary)"/><path d="M0 52 V36 a7 7 0 0 1 7-7 h7 a10 10 0 0 0-1 5 V52z" fill="var(--primary)"/><path d="M60 52 V36 a7 7 0 0 0-7-7 h-7 a10 10 0 0 1 1 5 V52z" fill="var(--primary)"/></svg>
</section>
<section class="stat" style="left:428px;width:169px">
  <h3>TOTAL PROPERTIES AREA</h3>
  <p class="value">$422,000.00 SQ.FT.</p>
  <svg width="56" height="56" viewBox="0 0 56 56"><g fill="var(--primary)"><rect x="24" y="10" width="8" height="36"/><rect x="10" y="24" width="36" height="8"/><path d="M28 0 L39 12 H17z M28 56 L17 44 H39z M0 28 L12 17 V39z M56 28 L44 39 V17z"/></g></svg>
</section>
<section class="stat" style="left:617px;width:168px">
  <h3>RENTED AREA</h3>
  <p class="value">$233,500.00 SQ.FT</p>
  <svg width="56" height="56" viewBox="0 0 56 56"><g fill="var(--primary)"><rect x="24" y="10" width="8" height="36"/><rect x="10" y="24" width="36" height="8"/><path d="M28 0 L39 12 H17z M28 56 L17 44 H39z M0 28 L12 17 V39z M56 28 L44 39 V17z"/></g></svg>
</section>
<section class="stat" style="left:806px;width:168px">
  <h3>VACANCIES AREA</h3>
  <p class="value">$188,500.00</p>
  <svg width="56" height="56" viewBox="0 0 56 56"><g fill="var(--primary)"><rect x="24" y="10" width="8" height="36"/><rect x="10" y="24" width="36" height="8"/><path d="M28 0 L39 12 H17z M28 56 L17 44 H39z M0 28 L12 17 V39z M56 28 L44 39 V17z"/></g></svg>
</section>

<div class="range" style="left:115px;width:128px"><svg width="13" height="13" viewBox="0 0 13 13"><circle cx="6.5" cy="6.5" r="5.5" fill="none" stroke="var(--primary)" stroke-width="1.8"/><path d="M6.5 3.5V7H4.5" fill="none" stroke="var(--primary)" stroke-width="1.5"/></svg>LAST 7 DAYS</div>
<div class="range" style="left:258px;width:127px"><svg width="13" height="13" viewBox="0 0 13 13"><circle cx="6.5" cy="6.5" r="5.5" fill="none" stroke="var(--primary)" stroke-width="1.8"/><path d="M6.5 3.5V7H4.5" fill="none" stroke="var(--primary)" stroke-width="1.5"/></svg>LAST MONTHS</div>
<div class="range" style="left:395px;width:142px"><svg width="13" height="13" viewBox="0 0 13 13"><circle cx="6.5" cy="6.5" r="5.5" fill="none" stroke="var(--primary)" stroke-width="1.8"/><path d="M6.5 3.5V7H4.5" fill="none" stroke="var(--primary)" stroke-width="1.5"/></svg>LAST 3 MONTHS</div>
<div class="range" style="left:546px;width:127px"><svg width="13" height="13" viewBox="0 0 13 13"><circle cx="6.5" cy="6.5" r="5.5" fill="none" stroke="var(--primary)" stroke-width="1.8"/><path d="M6.5 3.5V7H4.5" fill="none" stroke="var(--primary)" stroke-width="1.5"/></svg>NEXT 7 DAYS</div>
<div class="range" style="left:690px;width:127px"><svg width="13" height="13" viewBox="0 0 13 13"><circle cx="6.5" cy="6.5" r="5.5" fill="none" stroke="var(--primary)" stroke-width="1.8"/><path d="M6.5 3.5V7H4.5" fill="none" stroke="var(--primary)" stroke-width="1.5"/></svg>NEXT MONTHS</div>
<div class="range" style="left:829px;width:137px"><svg width="13" height="13" viewBox="0 0 13 13"><circle cx="6.5" cy="6.5" r="5.5" fill="none" stroke="var(--primary)" stroke-width="1.8"/><path d="M6.5 3.5V7H4.5" fill="none" stroke="var(--primary)" stroke-width="1.5"/></svg>NEXT 3 MONTHS</div>

<section class="chart-panel">
  <svg width="852" height="390" viewBox="0 0 852 390">
    <g fill="#111"><rect x="17" y="29" width="4" height="10"/><rect x="23" y="19" width="4" height="20"/><rect x="29" y="24" width="4" height="15"/></g>
    <text x="46" y="36" font-size="14.5">12/27/2021 - 01/03/2021</text>
    <g stroke="var(--grid)" stroke-width="1">
      <line x1="73" y1="70" x2="815" y2="70"/><line x1="73" y1="120" x2="815" y2="120"/><line x1="73" y1="170" x2="815" y2="170"/><line x1="73" y1="220" x2="815" y2="220"/><line x1="73" y1="270" x2="815" y2="270"/><line x1="73" y1="320" x2="815" y2="320"/><line x1="73" y1="70" x2="73" y2="320"/>
    </g>
    <g font-size="13.5" text-anchor="end">
      <text x="63" y="75">1.25</text><text x="63" y="125">1</text><text x="63" y="175">0.75</text><text x="63" y="225">0.5</text><text x="63" y="275">0.25</text><text x="63" y="325">0</text>
    </g>
    <rect x="363" y="120" width="54" height="200" rx="2" fill="var(--bar)"/>
    <g font-size="12.5" text-anchor="middle">
      <text x="110" y="345">12/27/2021</text><text x="205" y="345">12/28/2021</text><text x="301" y="345">12/29/2021</text><text x="396" y="345">12/30/2021</text><text x="492" y="345">12/31/2021</text><text x="590" y="345">12/01/20201</text><text x="683" y="345">12/02/2021</text><text x="778" y="345">12/03/2021</text>
    </g>
  </svg>
</section>

<div class="legend-item" style="left:124px;top:955px"><span class="swatch" style="background:var(--c-sched)"></span><span>Scheduled<br>Maintenance</span></div>
<div class="legend-item" style="left:340px;top:955px;padding-left:6px;gap:6px"><span class="swatch" style="background:var(--c-done)"></span><span>Completed Scheduled<br>Maintenance</span></div>
<div class="legend-item" style="left:557px;top:955px"><span class="swatch" style="background:var(--c-future)"></span><span>Future Scheduled<br>Maintenance</span></div>
<div class="legend-item" style="left:773px;top:955px"><span class="swatch" style="background:var(--c-orders)"></span><span>Scheduled Work<br>Orders</span></div>
<div class="legend-item" style="left:124px;top:1046px"><span class="swatch" style="background:var(--c-orders-done)"></span><span>Completed Work<br>Orders</span></div>
<div class="legend-item" style="left:340px;top:1046px;gap:10px"><span class="swatch" style="background:var(--c-insp)"></span><span>Property Inspections<br>&nbsp;in Progress</span></div>
<div class="legend-item" style="left:555px;top:1046px;gap:12px"><span class="swatch" style="background:var(--c-insp-done)"></span><span>Completed Property<br>Inspections</span></div>

<footer class="footer">© 2021 ERP SOFTWARE ALL RIGHTS RESERVED</footer>
</body>
</html>
```